Military and tactical gear supply company needs web design

We need a web design for a company called U.S. Vantrel. We provide quality tactical equipment to military and law enforcement. This is an e-commerce business and we primarily market ourselves on social media. Our key products are backpacks, military-style belts, and tactical flashlights. The gear we sell is not yet widely known about, but is on par with the state-of-the-art products in this field. We want the website to convey the message of quality, durability, and reliability. We use the word "kinetic" because the customers in this field are very "action-oriented" and we would like that idea to be communicated in the web site as well. The primary demographic is men in their 20's-30's, so the web site should have a masculine feel to it. Attached is the logo and color scheme.

```html
<!DOCTYPE html>
<html lang="en">
<head>
<meta charset="utf-8">
<title>U.S. Vantrel — Tactical Gear</title>
<link href="https://fonts.googleapis.com/css2?family=Ultra&family=Black+Ops+One&family=Lato:wght@400;700&display=swap" rel="stylesheet">
<style>
:root{
  --red:#a3182a;
  --blue:#28506e;
  --black:#161616;
  --ink:#333333;
  --line:#cfcfcf;
  --white:#ffffff;
}
*{box-sizing:border-box;margin:0;padding:0}
html,body{width:1200px;height:3259px;overflow:hidden}
body{position:relative;font-family:"Lato",sans-serif;color:var(--ink);background:var(--white);font-synthesis:none}
.abs{position:absolute}
.slab{font-family:"Ultra","Rockwell","Georgia",serif;font-weight:700;text-transform:uppercase}
.ops{font-family:"Black Ops One","Impact",sans-serif;font-weight:700;text-transform:uppercase}

/* top bar */
.topbar{left:0;top:0;width:1200px;height:53px;background:var(--black);color:#fff;font-size:13px;font-weight:700}
.topbar .ship{left:75px;top:18px;display:flex;align-items:center;gap:7px}
.topbar .icons{right:75px;top:21px;display:flex;gap:36px}
.topbar .icons span{width:10px;height:11px;background:#fff;border-radius:2px;display:block}

/* header */
.brand{font-family:"Lato",sans-serif;font-weight:700;font-size:40px;letter-spacing:2px;color:var(--blue);display:flex;align-items:center;gap:10px;white-space:nowrap}
.brand i{width:14px;height:14px;background:var(--red);display:block}
.header-brand{left:75px;top:90px}
.search{left:704px;top:92px;width:271px;height:49px;border:1px solid var(--line);font-size:15px;color:#555;padding:15px 14px}
.search svg{position:absolute;right:14px;top:16px}
.cart-btn{left:990px;top:92px;width:48px;height:48px;background:var(--red)}
.cart-btn svg{margin:17px 0 0 17px}
.cart-text{left:1049px;top:107px;font-size:13px;font-weight:700;color:var(--red)}

/* nav */
.nav{left:0;top:166px;width:1200px;height:49px;background:var(--blue)}
.nav ul{list-style:none;display:flex;position:absolute;left:75px;top:0;height:49px}
.nav li{color:#fff;font-size:14px;font-weight:700;line-height:49px;padding:0 16.5px;white-space:nowrap}
.nav li.active{background:var(--red);padding:0 14px}

/* hero */
.hero{left:0;top:215px;width:1200px;height:504px;background:linear-gradient(120deg,#4a3527 0%,#2b2420 40%,#1d1f24 60%,#5a4230 100%)}
.hero h1{position:absolute;left:0;width:1200px;top:138px;text-align:center;color:#fff;font-size:72px;line-height:80px}
.hero p{position:absolute;left:290px;width:620px;top:212px;text-align:center;color:#fff;font-size:25px;line-height:32px;font-weight:700}
.btn-white{background:#fff;color:var(--red);font-size:22px;text-align:center}
.hero .btn-white{position:absolute;left:519px;top:299px;width:162px;height:53px;line-height:53px}

/* categories */
.cat{top:753px;width:330px;height:376px}
.cat .label{position:absolute;left:26px;top:258px;width:278px;height:92px;background:#fff;color:var(--red);font-size:27px;line-height:32px;display:flex;align-items:center;justify-content:center;text-align:center}
.cat-1{left:75px;background:linear-gradient(160deg,#5b5a2a,#6d6a5e 50%,#3a3a25)}
.cat-2{left:435px;background:linear-gradient(160deg,#2b2d31,#1c1d20 50%,#6b4a35)}
.cat-3{left:796px;background:linear-gradient(160deg,#3a3f46,#8aa2b5 45%,#2a3226)}

/* welcome */
.welcome{left:0;top:1196px;width:1200px;height:403px;background:var(--blue);color:#fff;text-align:center}
.welcome h2{position:absolute;top:60px;width:1200px;font-size:44px;line-height:56px}
.welcome p{position:absolute;left:70px;width:1060px;top:130px;font-size:15px;line-height:28px;color:#fff}
.welcome .btn-white{position:absolute;left:519px;top:280px;width:162px;height:52px;line-height:52px}

/* products */
.products-title{left:0;top:1650px;width:1200px;text-align:center;font-size:42px;line-height:56px;color:var(--ink)}
.card{top:1730px;width:241px}
.card .thumb{width:241px;height:256px;border:2px solid var(--line);background:#fff;position:relative}
.card .thumb div{position:absolute;left:30px;top:30px;width:177px;height:192px}
.card h3{margin-top:26px;text-align:center;color:var(--red);font-size:22px}
.card p{text-align:center;font-size:15px;line-height:25px;margin-top:8px;color:var(--ink)}
.card .buy{margin:16px auto 0;width:162px;height:52px;line-height:52px;background:var(--blue);color:#fff;font-size:22px;text-align:center}

/* promos */
.promo{top:2236px;width:512px;height:350px;color:#fff;text-align:center}
.promo-1{left:75px;background:linear-gradient(135deg,#3e3229,#5a4434 55%,#2c2622)}
.promo-2{left:615px;background:linear-gradient(135deg,#5a3e28,#4d4a3a 55%,#2e2a22)}
.promo h2{position:absolute;left:0;width:512px}
.promo-1 .big{top:38px;font-size:72px;line-height:80px}
.promo-1 .sub{top:122px;font-size:50px;line-height:54px}
.promo-2 .big{top:70px;font-size:76px;line-height:72px}
.promo .btn-white{position:absolute;left:175px;top:254px;width:162px;height:52px;line-height:52px}

/* newsletter */
.newsletter{left:0;top:2655px;width:1200px;height:312px;background:var(--blue);color:#fff;text-align:center}
.newsletter h2{position:absolute;top:66px;width:1200px;font-size:42px;line-height:52px}
.newsletter p{position:absolute;top:131px;width:1200px;font-size:15px;color:#fff}
.newsletter .field{position:absolute;left:304px;top:185px;width:423px;height:52px;background:#fff;color:var(--ink);font-size:15px;text-align:left;padding:17px 17px}
.newsletter .btn-white{position:absolute;left:739px;top:185px;width:162px;height:52px;line-height:52px}

/* footer */
.footer-brand{left:76px;top:3040px}
.footer-brand.brand{font-size:32px}
.copy{left:76px;top:3100px;font-size:14px;line-height:25px;color:var(--ink)}
.social{left:76px;top:3170px;display:flex;gap:18px}
.social span{width:22px;height:22px;border-radius:50%;background:var(--ink);display:block}
.fcol{top:3024px}
.fcol h4{font-family:"Black Ops One","Impact",sans-serif;font-weight:700;font-size:18px;line-height:22px;color:var(--ink);margin-bottom:12px;text-transform:uppercase}
.fcol ul{list-style:none}
.fcol li{font-size:15px;line-height:31px;color:var(--ink)}
</style>
</head>
<body>

<div class="abs topbar">
  <div class="abs ship">
    <svg width="13" height="10" viewBox="0 0 13 10"><rect x="0" y="1" width="8" height="6" fill="#fff"/><path d="M8 3h3l2 2v2H8z" fill="#fff"/><circle cx="3" cy="8.5" r="1.5" fill="#fff"/><circle cx="10" cy="8.5" r="1.5" fill="#fff"/></svg>
    FREE SHIPPING
  </div>
  <div class="abs icons"><span></span><span></span><span></span><span></span></div>
</div>

<div class="abs brand header-brand"><i></i>US VANTREL</div>
<div class="abs search">Search..
  <svg width="14" height="14" viewBox="0 0 14 14"><circle cx="6" cy="6" r="4.5" stroke="#a3182a" stroke-width="2" fill="none"/><path d="M9.5 9.5L13 13" stroke="#a3182a" stroke-width="2"/></svg>
</div>
<div class="abs cart-btn"><svg width="14" height="13" viewBox="0 0 14 13"><path d="M0 1h3l2 7h7l2-5H4" stroke="#fff" stroke-width="1.6" fill="none"/><circle cx="6" cy="11" r="1.4" fill="#fff"/><circle cx="11" cy="11" r="1.4" fill="#fff"/></svg></div>
<div class="abs cart-text">MY CART (0)</div>

<nav class="abs nav">
  <ul>
    <li class="active">HOME</li><li>ABOUT US</li><li>BACKPACKS</li><li>MILITARY ATYLE BELTS</li><li>TACTICAL FLASHLIGHTS</li><li>SHOP</li><li>BLOG</li><li>REVIEWS</li><li>CONTACT US</li>
  </ul>
</nav>

<section class="abs hero" role="img" aria-label="Tactical flashlight and pouch on a weathered wooden table">
  <h1 class="slab">U.S. Vantrel</h1>
  <p>We provide quality tactical equipment to military and law enforcement.</p>
  <div class="btn-white ops">Read More</div>
</section>

<div class="abs cat cat-1" role="img" aria-label="Camouflage backpack resting on grass"><div class="label ops">Backpacks</div></div>
<div class="abs cat cat-2" role="img" aria-label="Hands fastening a military style belt"><div class="label ops">Military Style<br>Belts</div></div>
<div class="abs cat cat-3" role="img" aria-label="Close view of a lit tactical flashlight"><div class="label ops">Tactical<br>Flashlights</div></div>

<section class="abs welcome">
  <h2 class="slab">Welcome to U.S. Vantrel</h2>
  <p>Lorem ipsum dolor sit amet, consectetur adipiscing elit. Donec ultricies sapien arcu, nec tincidunt tellus placerat quis. Nunc vel sapien eros. Nunc viverra elit vel diam pellentesque, consectetur sodales purus dapibus. Vestibulum ac ligula vitae dui placerat iaculis sed eget augue. Nullam tincidunt nulla at urna bibendum, non congue turpis hendrerit. Aliquam nec luctus justo, sit amet laoreet nunc. Donec eleifend interdum neque quis condimentum. Cras consectetur maximus nisl et malesuada.</p>
  <div class="btn-white ops">Read More</div>
</section>

<h2 class="abs products-title slab">Our Products</h2>

<div class="abs card" style="left:76px">
  <div class="thumb"><div role="img" aria-label="Olive canvas belt with black buckle" style="background:radial-gradient(ellipse at center,#5b6137 0%,#4d5230 55%,#fff 72%)"></div></div>
  <h3 class="ops">Product Name</h3>
  <p>Neque porro quisquam est qui<br>dolorem ipsum</p>
  <div class="buy ops">Buy Now</div>
</div>
<div class="abs card" style="left:347px">
  <div class="thumb"><div role="img" aria-label="Olive military backpack" style="background:radial-gradient(ellipse at center,#4a5232 0%,#3f462b 50%,#fff 70%)"></div></div>
  <h3 class="ops">Product Name</h3>
  <p>Neque porro quisquam est qui<br>dolorem ipsum</p>
  <div class="buy ops">Buy Now</div>
</div>
<div class="abs card" style="left:618px">
  <div class="thumb"><div role="img" aria-label="Black zoom flashlight with lanyard" style="background:radial-gradient(ellipse at center,#222 0%,#333 25%,#fff 50%)"></div></div>
  <h3 class="ops">Product Name</h3>
  <p>Neque porro quisquam est qui<br>dolorem ipsum</p>
  <div class="buy ops">Buy Now</div>
</div>
<div class="abs card" style="left:887px">
  <div class="thumb"><div role="img" aria-label="Upright black tactical flashlight" style="background:linear-gradient(90deg,#fff 35%,#1c1c1c 38%,#2a2a2a 62%,#fff 65%)"></div></div>
  <h3 class="ops">Product Name</h3>
  <p>Neque porro quisquam est qui<br>dolorem ipsum</p>
  <div class="buy ops">Buy Now</div>
</div>

<div class="abs promo promo-1" role="img" aria-label="Tactical flashlights on a wooden surface">
  <h2 class="slab big">15% Off</h2>
  <h2 class="slab sub">Tactical<br>Flashlights</h2>
  <div class="btn-white ops">Shop Now</div>
</div>
<div class="abs promo promo-2" role="img" aria-label="Combat boots and camouflage pack against wooden planks">
  <h2 class="slab big">New<br>Arrivals</h2>
  <div class="btn-white ops">Shop Now</div>
</div>

<section class="abs newsletter">
  <h2 class="slab">Newsletter Sign Up</h2>
  <p>Donec ultricies sapien arcu, nec tincidunt tellus placerat unc viverra elit vel diam pellentesque, consectetur sodales purus dapibus</p>
  <div class="field">Enter Email Address</div>
  <div class="btn-white ops">Sign Up</div>
</section>

<div class="abs brand footer-brand"><i></i>US VANTREL</div>
<div class="abs copy">Copyright © 2020, Company Name<br>All Right reserved</div>
<div class="abs social" aria-label="Social links"><span></span><span></span><span></span><span></span><span></span><span></span></div>

<div class="abs fcol" style="left:371px">
  <h4>Navigation</h4>
  <ul><li>Home</li><li>About Us</li><li>Backpacks</li><li>Military style belts</li><li>Tactical Flashlights</li></ul>
</div>
<div class="abs fcol" style="left:537px;top:3058px">
  <ul><li>Shop</li><li>Blog</li><li>Reviews</li><li>Contact Us</li></ul>
</div>
<div class="abs fcol" style="left:684px">
  <h4>My Account</h4>
  <ul><li>Lorem ipsum dolor</li><li>Sit amet</li><li>Consectetur adipiscing</li><li>Donec ultricies</li></ul>
</div>
<div class="abs fcol" style="left:925px">
  <h4>Support</h4>
  <ul><li>Lorem ipsum dolor</li><li>Sit amet</li><li>Consectetur adipiscing</li><li>Donec ultricies</li></ul>
</div>

</body>
</html>
```